Technology, Futuristic Innovation & Artificial Intelligence

I am looking for something with Artificial Intelligence DNA strands....
Blue, black, with white dna strands........I like clean, crisp, professional and not busy look.................................................................................................................................................................................................................................................................................................................................................................................. Thanks!

Target Market(s)

Engineers and United States Government Contractors

Industry/Entity Type

Engineering

Contact Information for Business Card

I've uploaded my logo the certification logo.

Font styles to use
Serif

Colors
3176b5
33a6d7
ffffff

Requirements
Must have
• Name
• Title
• Address
• Phone number
• website name
• certification logo
Nice to have
• Something with Artificial Intelligence DNA strands......
• **Please note it would be nice to have the business card 3D or textured with raised images. Thanks
Should not have
• Please no feminine flowery designs....this is an engineering firm

```html
<!DOCTYPE html>
<html lang="en">
<head>
<meta charset="utf-8">
<title>Veltrana Business Card</title>
<link rel="stylesheet" href="https://fonts.googleapis.com/css2?family=Oswald:wght@500;600&family=Open+Sans:wght@400;600&display=swap">
<style>
  :root {
    --stage: #1c1c1e;
    --card-black: #141518;
    --card-graphite: #26282d;
    --blue-deep: #1d3fb8;
    --blue-mid: #3176b5;
    --blue-bright: #33a6d7;
    --white: #ffffff;
    --silver: #c9ccd2;
    --muted: #6b6e75;
    --badge: #3a3f6e;
    --stripe: #050608;
  }
  html, body {
    margin: 0;
    padding: 0;
    width: 1200px;
    height: 900px;
    overflow: hidden;
    background: var(--stage);
  }
  .canvas {
    position: relative;
    width: 1200px;
    height: 900px;
  }
  .card {
    position: absolute;
    width: 560px;
    height: 320px;
    border-radius: 22px;
    overflow: hidden;
    background: linear-gradient(160deg, var(--card-graphite), var(--card-black));
    box-shadow: 0 18px 40px rgba(0,0,0,0.55);
  }
  .card--front { left: 70px; top: 70px; }
  .card--back { left: 570px; top: 510px; }

  .circuit-field {
    position: absolute;
    left: 0;
    width: 100%;
    background: radial-gradient(ellipse at 55% 60%, var(--blue-bright) 0%, var(--blue-mid) 40%, var(--blue-deep) 100%);
  }
  .card--front .circuit-field { top: 0; height: 120px; }
  .card--back .circuit-field--top { top: 0; height: 88px; }
  .card--back .circuit-field--bottom { top: 258px; height: 62px; }

  .stripe-row {
    position: absolute;
    left: 0;
    width: 100%;
    height: 26px;
    background: repeating-linear-gradient(90deg, var(--stripe) 0 10px, transparent 10px 20px);
  }
  .card--front .stripe-row { top: 110px; }
  .card--back .stripe-row--top { top: 78px; }
  .card--back .stripe-row--bottom { top: 236px; }

  .edge-line {
    position: absolute;
    left: 0;
    width: 100%;
    height: 2px;
    background: linear-gradient(90deg, transparent, var(--silver), transparent);
  }
  .card--front .edge-line { top: 138px; }
  .card--back .edge-line--top { top: 104px; }
  .card--back .edge-line--bottom { top: 234px; }

  .cert-badges {
    position: absolute;
    display: flex;
    flex-direction: column;
    gap: 6px;
  }
  .card--front .cert-badges { left: 40px; top: 186px; }
  .card--back .cert-badges { left: 24px; top: 128px; }
  .cert-badge {
    width: 22px;
    height: 22px;
    background: var(--badge);
    border-radius: 3px;
  }

  .brand {
    position: absolute;
    display: flex;
    flex-direction: column;
    gap: 4px;
  }
  .card--front .brand { left: 76px; top: 196px; }
  .card--back .brand { left: 56px; top: 140px; }
  .brand__row {
    display: flex;
    align-items: center;
    gap: 10px;
  }
  .brand__mark {
    width: 18px;
    height: 18px;
    background: var(--blue-bright);
  }
  .brand__name {
    font-family: "Oswald", sans-serif;
    font-weight: 600;
    font-size: 40px;
    letter-spacing: 6px;
    color: var(--silver);
    line-height: 1;
  }
  .brand__tagline {
    font-family: "Open Sans", sans-serif;
    font-weight: 600;
    font-size: 9px;
    letter-spacing: 1.5px;
    color: var(--white);
    margin-left: 28px;
  }
  .card--back .brand__mark { width: 14px; height: 14px; }
  .card--back .brand__name { font-size: 30px; letter-spacing: 4px; }
  .card--back .brand__tagline { font-size: 8px; margin-left: 24px; }

  .website {
    position: absolute;
    right: 34px;
    top: 160px;
    margin: 0;
    font-family: "Open Sans", sans-serif;
    font-size: 13px;
    letter-spacing: 1px;
    color: var(--silver);
  }

  .contact {
    position: absolute;
    right: 30px;
    top: 106px;
    text-align: right;
    color: var(--white);
    font-family: "Open Sans", sans-serif;
  }
  .contact__name {
    font-family: "Oswald", sans-serif;
    font-weight: 600;
    font-size: 26px;
    letter-spacing: 1px;
    color: var(--silver);
    line-height: 1;
  }
  .contact__title {
    font-family: "Oswald", sans-serif;
    font-weight: 500;
    font-size: 12px;
    color: var(--muted);
    margin: 2px 0 10px;
  }
  .contact__line {
    display: flex;
    justify-content: flex-end;
    align-items: center;
    gap: 8px;
    font-size: 12.5px;
    margin-bottom: 5px;
  }
  .contact__icon { width: 13px; height: 13px; fill: var(--blue-bright); }
</style>
</head>
<body>
<main class="canvas">

  <section class="card card--front" aria-label="Business card front">
    <div class="circuit-field" role="img" aria-label="Glowing blue circuit board traces"></div>
    <div class="stripe-row"></div>
    <div class="edge-line"></div>
    <div class="cert-badges">
      <div class="cert-badge"></div>
      <div class="cert-badge"></div>
    </div>
    <div class="brand">
      <div class="brand__row">
        <span class="brand__mark"></span>
        <span class="brand__name">VELTRANA</span>
      </div>
      <span class="brand__tagline">DESIGNING THE NEXT WAVE</span>
    </div>
    <p class="website">WWW.VELTRANA.ORG</p>
  </section>

  <section class="card card--back" aria-label="Business card back">
    <div class="circuit-field circuit-field--top" role="img" aria-label="Glowing blue circuit board traces"></div>
    <div class="stripe-row stripe-row--top"></div>
    <div class="edge-line edge-line--top"></div>
    <div class="edge-line edge-line--bottom"></div>
    <div class="stripe-row stripe-row--bottom"></div>
    <div class="circuit-field circuit-field--bottom" role="img" aria-label="Glowing blue circuit board traces"></div>

    <div class="cert-badges">
      <div class="cert-badge"></div>
      <div class="cert-badge"></div>
    </div>
    <div class="brand">
      <div class="brand__row">
        <span class="brand__mark"></span>
        <span class="brand__name">VELTRANA</span>
      </div>
      <span class="brand__tagline">DESIGNING THE NEXT WAVE</span>
    </div>

    <div class="contact">
      <div class="contact__name">DANA WHITFORD</div>
      <div class="contact__title">CEO</div>
      <div class="contact__line">
        <span>dwhitford@veltrana.org</span>
        <svg class="contact__icon" viewBox="0 0 16 16" aria-hidden="true"><rect x="1" y="3" width="14" height="10" rx="1"/><path d="M1.5 4l6.5 5 6.5-5" fill="none" stroke="#141518" stroke-width="1.4"/></svg>
      </div>
      <div class="contact__line">
        <span>555.014.2290</span>
        <svg class="contact__icon" viewBox="0 0 16 16" aria-hidden="true"><path d="M3 1l3 3-2 2c1 2 3 4 5 5l2-2 3 3-2 3C6 15 1 10 0 4z"/></svg>
      </div>
      <div class="contact__line">
        <span>PO Box 318, Harbor Point, SC 29000</span>
        <svg class="contact__icon" viewBox="0 0 16 16" aria-hidden="true"><path d="M8 0a5 5 0 0 0-5 5c0 4 5 11 5 11s5-7 5-11a5 5 0 0 0-5-5zm0 7a2 2 0 1 1 0-4 2 2 0 0 1 0 4z"/></svg>
      </div>
    </div>
  </section>

</main>
</body>
</html>
```